Oil Field Service company needs professional business cards

Looking to clean up our current company business cards and look a little more professional. Brenwick Casing Services is a US based company that services the oil field. We deal with engineers, managers and oil rigs....................................................................................................................................................................................................................................................................................................................................................................................................

Target Market(s)

Oil and Gas professionals

Industry/Entity Type

Oil And Gas

Contact Information for Business Card

See attached photo as example

Font styles to use
Sans Serif

Colors
ec1f27

Requirements
Must have
• Company Logo, Name, Title, Cell, Office, Fax, Email.
• See attached photo
Nice to have
• External CRT, Internal CRT, Casing Crews, Torque Turn, Laydown Machine
Should not have
• Do not introduce any new pictures and keep it professional looking

```html
<!DOCTYPE html>
<html lang="en">
<head>
<meta charset="utf-8">
<title>Brenwick Casing Services – Business Cards</title>
<link rel="stylesheet" href="https://fonts.googleapis.com/css2?family=Open+Sans:wght@400;600;700&display=swap">
<style>
  :root{
    --page:#e9e9e7;
    --slate:#414f5b;
    --slate-text:#4b5661;
    --red:#ec1f27;
    --white:#ffffff;
    --muted:#d7dde2;
  }
  *{box-sizing:border-box;margin:0;padding:0}
  html,body{width:1200px;height:950px;overflow:hidden}
  body{
    background:var(--page);
    font-family:"Open Sans",Arial,sans-serif;
    position:relative;
  }
  .card{
    position:absolute;
    left:250px;
    width:700px;height:400px;
    overflow:hidden;
    box-shadow:0 6px 18px rgba(0,0,0,.18);
  }
  .card--front{top:50px;background:var(--white)}
  .card--back{top:500px;background:var(--slate)}

  .front-shape{position:absolute;inset:0}

  .brand{
    position:absolute;
    font-weight:700;
    text-transform:uppercase;
    line-height:1.05;
  }
  .brand span{display:block}
  .brand--front{left:48px;top:56px;color:var(--slate-text);font-size:34px;letter-spacing:3px}
  .brand--back{left:0;right:0;top:120px;text-align:center;color:var(--white);font-size:44px;letter-spacing:4px}

  .person{
    position:absolute;left:250px;top:262px;color:var(--white);
  }
  .person__name{font-size:25px;font-weight:600}
  .person__title,.person__place{font-size:15px;color:var(--muted);margin-top:3px}

  .contact{
    position:absolute;left:470px;top:150px;list-style:none;color:var(--white);
    font-size:15px;
  }
  .contact li{display:flex;align-items:center;gap:10px;height:25px}
  .contact svg{width:14px;height:14px;flex:none}

  .services{
    position:absolute;left:0;right:0;top:268px;text-align:center;
    color:var(--white);font-size:18px;line-height:1.6;letter-spacing:.5px;
  }
</style>
</head>
<body>

<section class="card card--front" aria-label="Business card front">
  <svg class="front-shape" viewBox="0 0 700 400" aria-hidden="true">
    <path d="M150 400 Q310 130 660 0 L700 0 L700 400 Z" fill="var(--red)"/>
    <path d="M200 400 Q340 160 700 28 L700 400 Z" fill="var(--slate)"/>
  </svg>

  <div class="brand brand--front">
    <span>Brenwick</span>
    <span>Casing Services</span>
  </div>

  <div class="person">
    <p class="person__name">Cody Hallmark</p>
    <p class="person__title">Area Manager</p>
    <p class="person__place">Redstone, OK 73990</p>
  </div>

  <ul class="contact">
    <li>
      <svg viewBox="0 0 16 16"><path fill="#fff" d="M3.5 1l3 3-1.6 1.8a9 9 0 0 0 5.3 5.3L12 9.5l3 3-2 2.2C7 14 2 9 1.3 3z"/></svg>
      (555)410-2200
    </li>
    <li>
      <svg viewBox="0 0 16 16"><rect x="4" y="1" width="8" height="14" rx="1.5" fill="none" stroke="#fff" stroke-width="1.5"/><circle cx="8" cy="12.5" r="1" fill="#fff"/></svg>
      (555)410-7731
    </li>
    <li>
      <svg viewBox="0 0 16 16"><rect x="1.5" y="5" width="13" height="9" rx="1" fill="none" stroke="#fff" stroke-width="1.5"/><rect x="4" y="1.5" width="8" height="4" fill="none" stroke="#fff" stroke-width="1.3"/></svg>
      (555)410-2290
    </li>
    <li>
      <svg viewBox="0 0 16 16"><rect x="1" y="3" width="14" height="10" rx="1" fill="none" stroke="#fff" stroke-width="1.5"/><path d="M1.5 3.5L8 9l6.5-5.5" fill="none" stroke="#fff" stroke-width="1.5"/></svg>
      cody@brenwick.com
    </li>
    <li>
      <svg viewBox="0 0 16 16"><circle cx="8" cy="8" r="6.5" fill="none" stroke="#fff" stroke-width="1.5"/><path d="M1.5 8h13M8 1.5c-3 3.5-3 9.5 0 13M8 1.5c3 3.5 3 9.5 0 13" fill="none" stroke="#fff" stroke-width="1.2"/></svg>
      www.brenwick.com
    </li>
  </ul>
</section>

<section class="card card--back" aria-label="Business card back">
  <div class="brand brand--back">
    <span>Brenwick</span>
    <span>Casing Services</span>
  </div>
  <p class="services">
    External CRT • Internal CRT • Casing Crews<br>
    Torque Turn • Laydown Machine
  </p>
</section>

</body>
</html>
```